Cognitive therapist.

I am a therapist and my main work is with clients who have depression and anxiety disorders.

I need something reasonably plain. Cognitive therapy is a very pragmatic approach to dealing with problems, so it isn't new agey (no offence to new age therapies at all)
Updates

Hi everyone, I am currently looking at a particular design that I will most likely go with. Cheers, Meg

Industry/Entity Type

Work

Contact Information for Business Card

Meg Tarvish
Cognitive Therapist
BA, PG Dip Mental Health,
PG Dip Cog Beh Therapy
MKTPR

The Quarry Lodge,
Level One
48 Marlow Parade
Cnr Fenwick St & Marlow Parade
P O Box 38 219
WELLINGTON 6143

Phone: 021 574 3082 Email: mtarvish@quellnet.co.nz

www.megtarvish.co.nz

Requirements
Should not have
• No illustration, or colour. not old style fonts.

```html
<!DOCTYPE html>
<html lang="en">
<head>
<meta charset="utf-8">
<title>Meg Tarvish – Business Card</title>
<link rel="stylesheet" href="https://fonts.googleapis.com/css2?family=Poppins:wght@600&family=Questrial&display=swap">
<style>
  :root {
    --backdrop: #3b3d42;
    --card: #ffffff;
    --teal: #6dc9b6;
    --ink: #555759;
    --ink-dark: #3a3b3d;
    --rule: #8a8c8e;
  }
  * { margin: 0; padding: 0; box-sizing: border-box; }
  html, body {
    width: 1200px; height: 1000px; overflow: hidden;
    background: var(--backdrop);
  }
  .canvas {
    position: relative; width: 1200px; height: 1000px;
    display: flex; align-items: center; justify-content: center;
  }
  .card {
    position: relative; width: 1000px; height: 610px;
    background: var(--card); border-radius: 44px; overflow: hidden;
    font-family: "Questrial", sans-serif; color: var(--ink);
  }
  .identity {
    position: absolute; right: 500px; top: 150px;
    text-align: right;
  }
  .identity__name {
    font-family: "Poppins", sans-serif; font-weight: 600;
    font-size: 54px; line-height: 1; letter-spacing: 1px;
    color: var(--teal); text-transform: uppercase;
  }
  .identity__credentials {
    margin-top: 6px; font-size: 25px; line-height: 1.22; color: var(--ink);
  }
  .divider {
    position: absolute; left: 520px; top: 128px;
    width: 1.5px; height: 200px; background: var(--rule);
  }
  .contact {
    position: absolute; left: 545px; top: 126px;
    font-size: 20px; line-height: 1.3; color: var(--ink);
  }
  .contact__pobox strong { color: var(--ink-dark); font-weight: 700; }
  .contact__list { list-style: none; margin-top: 8px; }
  .contact__item { display: flex; align-items: center; gap: 6px; }
  .contact__icon { width: 20px; height: 20px; flex: none; }
  .web-band {
    position: absolute; left: 0; right: 0; top: 470px;
    display: flex; align-items: center; gap: 14px;
  }
  .web-band__bar { height: 13px; background: var(--teal); }
  .web-band__bar--lead { width: 505px; }
  .web-band__bar--tail { flex: 1; }
  .web-band__url { font-size: 34px; color: var(--ink); white-space: nowrap; }
</style>
</head>
<body>
<main class="canvas">
  <article class="card">
    <section class="identity">
      <h1 class="identity__name">Meg Tarvish</h1>
      <p class="identity__credentials">
        Cognitive Therapist BA,<br>
        PG Dip Mental Health,<br>
        PG Dip Cog Beh Therapy MKTPR
      </p>
    </section>

    <div class="divider" aria-hidden="true"></div>

    <section class="contact">
      <address style="font-style: normal;">
        The Quarry Lodge, Level One<br>
        48 Marlow Parade Cnr Fenwick St<br>
        &amp; Marlow Parade<br>
        <span class="contact__pobox"><strong>P O Box</strong> 38 219 WELLINGTON 6143</span>
      </address>
      <ul class="contact__list">
        <li class="contact__item">
          <svg class="contact__icon" viewBox="0 0 20 20" aria-label="Phone">
            <circle cx="10" cy="10" r="10" fill="var(--teal)"/>
            <rect x="7" y="4.5" width="6" height="11" rx="1.2" fill="none" stroke="#fff" stroke-width="1.4"/>
            <circle cx="10" cy="13.3" r="0.8" fill="#fff"/>
          </svg>
          <span>021 574 3082</span>
        </li>
        <li class="contact__item">
          <svg class="contact__icon" viewBox="0 0 20 20" aria-label="Email">
            <circle cx="10" cy="10" r="10" fill="var(--teal)"/>
            <rect x="5" y="6.5" width="10" height="7" fill="none" stroke="#fff" stroke-width="1.3"/>
            <path d="M5 6.8 L10 10.8 L15 6.8" fill="none" stroke="#fff" stroke-width="1.3"/>
          </svg>
          <span>mtarvish@quellnet.co.nz</span>
        </li>
      </ul>
    </section>

    <div class="web-band">
      <span class="web-band__bar web-band__bar--lead"></span>
      <span class="web-band__url">www.megtarvish.co.nz</span>
      <span class="web-band__bar web-band__bar--tail"></span>
    </div>
  </article>
</main>
</body>
</html>
```